Velmora Freightway Solutions Business cards

Would like a very unique design catchy but professional for business cards. Please use log provided.Marlon WellsCeo and Founder TransCon Logistix Solutions1-888-913-3225mwells@tlsolutionsus.comwww.tlsolutionsus.com

```html
<!DOCTYPE html>
<html lang="en">
<head>
<meta charset="utf-8">
<title>Velmora Freightway Solutions – Business Cards</title>
<link rel="stylesheet" href="https://fonts.googleapis.com/css2?family=Montserrat:wght@500;600;700&family=Open+Sans:wght@400;600&display=swap">
<style>
  :root {
    --backdrop: #1d1d1f;
    --card: #ffffff;
    --brand-blue: #1273c2;
    --brand-red: #e8202a;
    --ink: #2a2a2a;
    --divider: #cfcfcf;
  }
  * { box-sizing: border-box; margin: 0; padding: 0; }
  html, body { width: 1200px; height: 960px; overflow: hidden; }
  body {
    background: var(--backdrop);
    position: relative;
    font-family: "Open Sans", Arial, sans-serif;
  }
  .card {
    position: absolute;
    width: 620px;
    height: 354px;
    background: var(--card);
    overflow: hidden;
  }

  /* Front */
  .card--front { left: 440px; top: 80px; }
  .front-brand {
    position: absolute;
    left: 0; right: 0; top: 110px;
    display: flex; align-items: center; justify-content: center; gap: 18px;
  }
  .front-brand__square { width: 46px; height: 46px; background: var(--brand-red); }
  .front-brand__name {
    font-family: "Montserrat", Arial, sans-serif;
    font-weight: 700;
    font-size: 34px;
    line-height: 1.1;
    color: var(--brand-blue);
  }
  .front-url {
    position: absolute;
    left: 60px; right: 60px; top: 262px;
    display: flex; align-items: center; gap: 16px;
  }
  .front-url__rule { flex: 1; height: 2px; background: var(--brand-blue); }
  .front-url__text {
    font-family: "Montserrat", Arial, sans-serif;
    font-weight: 600; font-size: 17px; letter-spacing: 3px;
    color: var(--ink);
  }
  .front-url__text span { color: var(--brand-blue); font-style: normal; }

  /* Back */
  .card--back { left: 160px; top: 530px; }
  .accent { position: absolute; background: var(--brand-blue); }
  .accent--left-bar { left: 0; top: 52px; width: 16px; height: 250px; }
  .accent--left-foot { left: 0; top: 286px; width: 70px; height: 16px; }
  .accent--right-top { right: 0; top: 20px; width: 96px; height: 16px; }
  .accent--right-bar { right: 0; top: 20px; width: 16px; height: 190px; }

  .back-brand {
    position: absolute; left: 50px; top: 105px; width: 250px;
  }
  .back-brand__row { display: flex; align-items: center; gap: 12px; }
  .back-brand__square { width: 26px; height: 26px; background: var(--brand-red); flex: none; }
  .back-brand__name {
    font-family: "Montserrat", Arial, sans-serif;
    font-weight: 700; font-size: 22px; line-height: 1.15;
    color: var(--brand-blue);
  }
  .back-brand__rule { margin-top: 14px; height: 2px; background: var(--brand-red); width: 230px; }

  .divider {
    position: absolute; left: 328px; top: 60px; width: 1px; height: 230px;
    background: var(--divider);
  }
  .contact { position: absolute; left: 350px; top: 62px; width: 240px; }
  .contact__name {
    font-family: "Montserrat", Arial, sans-serif;
    font-weight: 600; font-size: 21px; text-transform: uppercase;
    color: var(--brand-blue);
  }
  .contact__role {
    font-family: "Montserrat", Arial, sans-serif;
    font-weight: 500; font-size: 15px; text-transform: uppercase;
    color: var(--brand-red); margin-top: 2px;
  }
  .contact__address { font-size: 14px; color: var(--ink); margin-top: 16px; line-height: 1.4; }
  .contact__list { list-style: none; margin-top: 14px; }
  .contact__item {
    display: flex; align-items: center; gap: 10px;
    font-size: 14px; color: var(--ink); margin-bottom: 8px;
  }
  .contact__icon { width: 14px; height: 14px; flex: none; }
</style>
</head>
<body>

<section class="card card--front" aria-label="Card front">
  <div class="front-brand">
    <span class="front-brand__square"></span>
    <span class="front-brand__name">Velmora Freightway<br>Solutions</span>
  </div>
  <div class="front-url">
    <span class="front-url__rule"></span>
    <span class="front-url__text">www.<span>vfwayroutes</span>.com</span>
    <span class="front-url__rule"></span>
  </div>
</section>

<section class="card card--back" aria-label="Card back">
  <span class="accent accent--left-bar"></span>
  <span class="accent accent--left-foot"></span>
  <span class="accent accent--right-top"></span>
  <span class="accent accent--right-bar"></span>

  <div class="back-brand">
    <div class="back-brand__row">
      <span class="back-brand__square"></span>
      <span class="back-brand__name">Velmora Freightway Solutions</span>
    </div>
    <div class="back-brand__rule"></div>
  </div>

  <span class="divider"></span>

  <div class="contact">
    <p class="contact__name">Dorian Pike</p>
    <p class="contact__role">CEO and Founder</p>
    <p class="contact__address">4415 Calder Ridge Rd<br>Marlow, GA 30388</p>
    <ul class="contact__list">
      <li class="contact__item">
        <svg class="contact__icon" viewBox="0 0 16 16"><circle cx="8" cy="8" r="8" fill="#1273c2"/><path d="M5.5 4.5l1.5 0 .6 2-1 .8a5 5 0 0 0 2.1 2.1l.8-1 2 .6v1.5c0 .5-.5.9-1 .8A7 7 0 0 1 4.7 5.5c-.1-.5.3-1 .8-1z" fill="#fff"/></svg>
        1-888-470-6158
      </li>
      <li class="contact__item">
        <svg class="contact__icon" viewBox="0 0 16 16"><circle cx="8" cy="8" r="8" fill="#1273c2"/><rect x="4" y="5" width="8" height="6" fill="#fff"/><path d="M4 5l4 3.2L12 5" stroke="#1273c2" fill="none"/></svg>
        dpike@vfwayroutes.com
      </li>
      <li class="contact__item">
        <svg class="contact__icon" viewBox="0 0 16 16"><circle cx="8" cy="8" r="8" fill="#1273c2"/><circle cx="8" cy="8" r="4.5" fill="none" stroke="#fff"/><ellipse cx="8" cy="8" rx="2" ry="4.5" fill="none" stroke="#fff"/><line x1="3.5" y1="8" x2="12.5" y2="8" stroke="#fff"/></svg>
        www.vfwayroutes.com
      </li>
    </ul>
  </div>
</section>

</body>
</html>
```